Business Card for beauty technology startup

Design Glimora Business Card for a Beauty, based on the website identity and colors (https://www.glimora-example.com).
Glimora is a beauty tech startup that gathers helpful product info for beauty lovers and consumers (such as availability on stores, price range and product reviews) for makeup products. The card design must be young, colorful but clean, and very modern.

Target Market(s)

woman, 15-35

Industry/Entity Type

Cosmetics

Contact Information for Business Card

Full Name, address, phone

Font styles to use
Other font styles liked:
• Advent Pro

Colors
e34297
86cfc6
ffffff
5c5c5c
e8e8e8
e667a6
b2b2b2

Requirements
Must have
• One full colored side with a creative design and another with card info
• Use Color palette: #95C5C5 and/or #D38AA5
• Use fonts: Advent Pro
• Use website identity: https://www.glimora-example.com
Nice to have
• If needed extra font: Roboto

```html
<!DOCTYPE html>
<html lang="en">
<head>
<meta charset="utf-8">
<title>Glimora Business Card</title>
<link rel="stylesheet" href="https://fonts.googleapis.com/css2?family=Josefin+Sans:wght@300&family=Montserrat:wght@400;500;600&display=swap">
<style>
  :root {
    --canvas: #e6e6e6;
    --plum: #46323f;
    --paper: #ffffff;
    --rose: #c07c9b;
    --rose-strong: #b2668a;
    --ink: #4a4a4a;
    --muted: #7a7a7a;
  }
  * { margin: 0; padding: 0; box-sizing: border-box; }
  html, body { width: 1200px; height: 800px; overflow: hidden; }
  body {
    background: var(--canvas);
    font-family: "Montserrat", sans-serif;
    display: flex;
    align-items: center;
    justify-content: center;
    gap: 48px;
  }
  .card {
    position: relative;
    width: 532px;
    height: 304px;
    box-shadow: 0 4px 14px rgba(0,0,0,0.12);
    overflow: hidden;
  }

  /* Front: contact details */
  .card-front { background: var(--paper); }
  .edge-rule {
    position: absolute;
    left: 22px; top: 150px; bottom: 0;
    width: 1.5px;
    background: var(--rose);
  }
  .brand-mark {
    position: absolute;
    left: 4px; top: 112px;
    width: 40px; height: 40px;
    border: 2px solid var(--rose);
    border-radius: 50%;
    background: var(--paper);
  }
  .brand-name {
    position: absolute;
    left: 58px; top: 112px;
    font-family: "Josefin Sans", sans-serif;
    font-weight: 300;
    font-size: 34px;
    letter-spacing: 9px;
    color: var(--rose);
    text-transform: uppercase;
  }
  .person {
    position: absolute;
    right: 40px; top: 52px;
    text-align: right;
  }
  .person-name {
    font-weight: 600;
    font-size: 17px;
    letter-spacing: 0.5px;
    color: var(--rose-strong);
    text-transform: uppercase;
  }
  .person-role {
    font-size: 9px;
    letter-spacing: 0.8px;
    color: var(--muted);
    text-transform: uppercase;
    margin-top: 2px;
  }
  .name-rule {
    position: absolute;
    right: 40px; top: 96px;
    width: 300px; height: 1.5px;
    background: var(--rose);
  }
  .contact-rule {
    position: absolute;
    left: 74px; top: 210px;
    width: 220px; height: 1.5px;
    background: var(--rose);
  }
  .contact-list {
    position: absolute;
    left: 74px; top: 222px;
    list-style: none;
  }
  .contact-list li {
    display: flex;
    align-items: center;
    gap: 10px;
    font-size: 13px;
    line-height: 20px;
    color: var(--ink);
  }
  .contact-list svg { width: 10px; height: 10px; flex: none; }
  .address {
    position: absolute;
    right: 40px; top: 170px;
    text-align: right;
    font-size: 13px;
    line-height: 20px;
    color: var(--ink);
  }

  /* Back: brand side */
  .card-back {
    background: var(--plum);
    display: flex;
    align-items: center;
    justify-content: center;
    gap: 18px;
  }
  .back-mark {
    width: 46px; height: 46px;
    border: 3px solid var(--paper);
    border-radius: 50%;
  }
  .back-name {
    font-family: "Josefin Sans", sans-serif;
    font-weight: 300;
    font-size: 40px;
    letter-spacing: 10px;
    color: var(--paper);
    text-transform: uppercase;
  }
</style>
</head>
<body>
  <section class="card card-front" aria-label="Business card, contact side">
    <div class="edge-rule"></div>
    <div class="brand-mark"></div>
    <div class="brand-name">Glimora</div>

    <div class="person">
      <div class="person-name">Dana Verell</div>
      <div class="person-role">Owner</div>
    </div>
    <div class="name-rule"></div>

    <div class="address">48 Palm Row<br>Harbor City, FL 30010</div>

    <div class="contact-rule"></div>
    <ul class="contact-list">
      <li>
        <svg viewBox="0 0 10 10" aria-hidden="true"><path d="M2 1 L4 1 L4.5 3 L3.4 3.8 Q4.3 5.8 6.2 6.6 L7 5.5 L9 6 L9 8 Q5 9 1.5 4.5 Q1 2.5 2 1 Z" fill="var(--rose)"/></svg>
        555.014.2290
      </li>
      <li>
        <svg viewBox="0 0 10 10" aria-hidden="true"><rect x="1" y="2" width="8" height="6" fill="none" stroke="var(--rose)" stroke-width="1.2"/><path d="M1 2 L5 5.5 L9 2" fill="none" stroke="var(--rose)" stroke-width="1.2"/></svg>
        info@glimora-example.com
      </li>
      <li>
        <svg viewBox="0 0 10 10" aria-hidden="true"><circle cx="5" cy="5" r="4" fill="none" stroke="var(--rose)" stroke-width="1.2"/><path d="M1 5 H9 M5 1 Q2.5 5 5 9 Q7.5 5 5 1" fill="none" stroke="var(--rose)" stroke-width="0.9"/></svg>
        www.glimora-example.com
      </li>
    </ul>
  </section>

  <section class="card card-back" aria-label="Business card, brand side">
    <div class="back-mark"></div>
    <div class="back-name">Glimora</div>
  </section>
</body>
</html>
```